Letterhead and matching envelope design for a dental office

We need a new stationary design, letterhead and envelope #10, for a dental office in Denver area. We are called Bright Harbor Dental. We want a simple and minimalistic design but not a boring design. I wish to have one good point that makes it look professional. I have attached our logo. Feel free to use either one. I want the design for letterhead and envelope look like a "matching pair" but not look the same. The envelope doesn't have to be white and it will have an address window on bottom left.

Target Market(s)

everyone who visits dentist (adults)

Industry/Entity Type

Dental

Font styles to use
Other font styles liked:
• close to font on logo or something that matches well

Requirements
Must have
• professional
• simple, minimalistic
• unique point that stands out
Nice to have
• matching but not same design for letterhead and envelope
Should not have
• not look like all the other boring designs
• no flowery, distracting feats

```html
<!DOCTYPE html>
<html lang="en">
<head>
<meta charset="utf-8">
<title>Bright Harbor Dental — Envelope #10</title>
<link href="https://fonts.googleapis.com/css2?family=Lato:wght@400;700&family=Cormorant+Garamond:wght@500&display=swap" rel="stylesheet">
<style>
  :root {
    --backdrop: #c9c9c9;
    --paper: #ffffff;
    --brand-green: #3ab54a;
    --mint-band: #b9dfbc;
    --ink: #1e1e1e;
    --rule-grey: #a9a9a9;
    --box-border: #b5b5b5;
  }
  * { box-sizing: border-box; margin: 0; padding: 0; }
  html, body { width: 1200px; height: 848px; overflow: hidden; }
  body {
    background: var(--backdrop);
    font-family: "Lato", Arial, sans-serif;
    position: relative;
  }
  .envelope-front, .envelope-back {
    position: absolute;
    left: 220px;
    width: 760px;
    height: 330px;
    background: var(--paper);
  }
  .envelope-front { top: 82px; }
  .envelope-back { top: 430px; }

  .brand-name {
    position: absolute;
    left: 33px;
    top: 96px;
    font-family: "Lato", Arial, sans-serif;
    font-weight: 700;
    font-size: 19px;
    letter-spacing: 1.5px;
    text-transform: uppercase;
    color: var(--brand-green);
  }
  .return-address {
    position: absolute;
    left: 32px;
    top: 153px;
    font-size: 12.5px;
    line-height: 17px;
    color: var(--ink);
  }
  .return-address .sender { color: var(--brand-green); }

  .address-window {
    position: absolute;
    left: 33px;
    top: 205px;
    width: 294px;
    height: 101px;
    border: 1px solid var(--box-border);
    border-radius: 8px;
    padding: 8px 10px 0;
  }
  .address-window .label {
    font-family: "Cormorant Garamond", Georgia, serif;
    font-size: 10px;
    color: #666;
    letter-spacing: .5px;
  }
  .address-window .line {
    height: 16px;
    border-bottom: 1px dashed var(--rule-grey);
  }
  .address-window .line:first-of-type { height: 4px; }

  .footer-band {
    position: absolute;
    left: 0;
    bottom: 0;
    width: 100%;
    height: 8px;
    background: var(--mint-band);
  }
  .web-tab {
    position: absolute;
    left: 475px;
    bottom: 0;
    width: 216px;
    height: 26px;
  }
  .web-tab span {
    position: absolute;
    inset: 0;
    display: flex;
    align-items: center;
    justify-content: center;
    color: #fff;
    font-size: 12px;
    padding-top: 2px;
  }

  .flap { position: absolute; left: 0; top: 0; }
  .flap-mark {
    position: absolute;
    left: 342px;
    top: 27px;
    width: 76px;
    height: 76px;
    border: 1.5px solid #fff;
    border-radius: 50%;
    display: flex;
    flex-direction: column;
    align-items: center;
    justify-content: center;
    color: #fff;
    font-family: "Lato", Arial, sans-serif;
    font-weight: 700;
    font-size: 8.5px;
    letter-spacing: 1.2px;
    line-height: 12px;
    text-transform: uppercase;
    text-align: center;
  }
</style>
</head>
<body>

<section class="envelope-front" aria-label="Envelope front">
  <div class="brand-name">Bright Harbor Dental</div>

  <address class="return-address" style="font-style:normal">
    <div class="sender">Bright Harbor Dental</div>
    <div>2875 Larkspur Ave, Suite 210 Westminster, CO 80031</div>
  </address>

  <div class="address-window">
    <div class="label">TO</div>
    <div class="line"></div>
    <div class="line"></div>
    <div class="line"></div>
    <div class="line"></div>
    <div class="line"></div>
  </div>

  <div class="footer-band"></div>
  <div class="web-tab">
    <svg width="216" height="26" viewBox="0 0 216 26">
      <polygon points="0,26 20,0 196,0 216,26" fill="var(--paper)"/>
      <polygon points="6,26 24,0 192,0 208,26" fill="var(--brand-green)"/>
    </svg>
    <span>www.brightharbordental.com</span>
  </div>
</section>

<section class="envelope-back" aria-label="Envelope back">
  <svg class="flap" width="760" height="140" viewBox="0 0 760 140">
    <path d="M0 0 H760 C752 30 752 62 718 68 L420 126 Q380 134 340 126 L42 68 C8 62 8 30 0 0 Z" fill="var(--brand-green)"/>
  </svg>
  <div class="flap-mark">Bright<br>Harbor<br>Dental</div>
</section>

</body>
</html>
```